Website Update for Global Company - Solar Technology - LeafCore

We recently released our first version of our website velirox.com. However despite a longer process of developing the page, it is still missing the elements of a brilliant website. (Currently it looks dead and boring) We are having problems integrating our logo and want to create a more catching site. The task involves an updated and without changing most of main elements in the existing page. (Unless you can do it even better) The blue color needs to be kept but can be changed within the blue-spectrum. The logo text (VELIROX) must be better integrated in the site, however the main logo could be used in elements like we have tried with the background. The surface of the logo could be changed to 3D or metallic, or any other theme that would make the site more complete.
It would be good if some elements of the site could be used on business cards and invoices to keep the company identity.
Velirox is a new development company specialized in green energy and sustainable development. We do design, engineering, manufacturing, sourcing and other processes related to product development – both as consultants and for own products.
Keep the look of the site as professional as possible, and with a cooperate-looking style.

Link to existing page: www.velirox.com

Brief Update : After reviewing the designs we would like all new and current designers to make more bold designs that stands out from the rest. We do not like the standard layout that looks like any other cooperate homepage. We want a very unique and very lively page - with faded images and effects when hoovering like seen on our existing page. Try make all elements blend together, and use faded background images instead of just white color - or something else.

Make the site unique !

Industry/Entity Type

Solar Energy

Contact Information for Business Card

Owner/Founder/CEO : Jonas Ulfkær Lindholm
Company name: Velirox ApS
Email: jonas.ulfkaer@velirox.dk
Phone: +45 71 82 64 93
Slogan Sustainable Development
Address: Kildevej 58, 2
DK-5700 Svendborg, Denmark

Number of Pages Required

3 page

Font styles to use
Serif
Sans Serif

Colors
0555a3
85acd3
cedeed
3176b5
cee9f5
85cae6
0293ce
86cfc6
33b8a4

```html
<!DOCTYPE html>
<html lang="en">
<head>
<meta charset="utf-8">
<title>Velirox – Sustainable Development</title>
<link href="https://fonts.googleapis.com/css2?family=Raleway:wght@400;600;700;800&family=Open+Sans:wght@400;600;700&display=swap" rel="stylesheet">
<style>
:root{
  --blue-deep:#0555a3;
  --blue-mid:#3176b5;
  --blue-bright:#0293ce;
  --blue-soft:#85cae6;
  --blue-pale:#cee9f5;
  --blue-mist:#cedeed;
  --ink:#1e2225;
  --ink-2:#2a2f33;
  --text:#333a40;
  --muted:#8a9096;
  --line:#d9dde1;
  --white:#ffffff;
  --grey-band:#e4e6e8;
}
*{box-sizing:border-box;margin:0;padding:0}
html,body{width:1200px;height:2800px;overflow:hidden}
body{position:relative;font-family:"Open Sans",Arial,sans-serif;color:var(--text);background:var(--white)}
.heading{font-family:"Raleway",Arial,sans-serif}

/* header */
.site-header{position:absolute;left:0;top:0;width:1200px;height:120px;background:linear-gradient(180deg,#2a2e32,#1b1e21)}
.brand{position:absolute;left:100px;top:34px;display:flex;align-items:center;gap:14px}
.brand-mark{width:42px;height:42px;background:var(--blue-bright)}
.brand-name{font-family:"Raleway",sans-serif;font-weight:800;font-size:36px;letter-spacing:4px;color:var(--white)}
.account-links{position:absolute;right:100px;top:16px;font-size:12px;color:#c8ccd0;display:flex;gap:18px;letter-spacing:.5px}
.search-box{position:absolute;right:100px;top:56px;width:250px;height:30px;border:1px solid #4a5056;background:#25292c;color:#8c9298;font-size:12px;padding:6px 10px}
.search-box svg{position:absolute;right:8px;top:7px}

/* nav */
.main-nav{position:absolute;left:0;top:120px;width:1200px;height:36px;background:var(--blue-bright);display:flex;justify-content:center}
.main-nav a{display:block;width:142px;text-align:center;line-height:36px;font-size:12px;font-weight:700;color:var(--white);text-decoration:none;letter-spacing:.8px;border-right:1px solid rgba(255,255,255,.25)}
.main-nav a:first-child{border-left:1px solid rgba(255,255,255,.25);background:var(--blue-deep)}

/* hero */
.hero{position:absolute;left:0;top:156px;width:1200px;height:588px;overflow:hidden}
.hero-photo{position:absolute;inset:0;background:radial-gradient(ellipse at 60% 65%,#f3f5f7 0%,#d5dde4 45%,#9fb0bf 80%,#7f93a6 100%)}
.slider-dots{position:absolute;left:560px;top:556px;display:flex;gap:8px}
.slider-dots span{width:10px;height:10px;border-radius:50%;background:rgba(255,255,255,.7)}
.slider-dots span:first-child{background:var(--blue-bright)}

/* welcome */
.welcome{position:absolute;left:0;top:744px;width:1200px;height:596px;background:linear-gradient(180deg,#ffffff,#f3f6f9)}
.welcome h1{position:absolute;top:60px;width:100%;text-align:center;font-size:26px;font-weight:800;color:var(--ink-2);letter-spacing:1px}
.welcome .intro{position:absolute;left:220px;top:116px;width:760px;text-align:center;font-size:12px;line-height:20px;color:var(--muted)}
.btn{display:inline-block;height:36px;line-height:34px;padding:0 26px;font-size:11px;font-weight:700;letter-spacing:1px;text-decoration:none}
.btn-solid{background:var(--blue-deep);color:var(--white);border:1px solid var(--blue-deep)}
.btn-outline{border:1px solid var(--blue-deep);color:var(--blue-deep);background:var(--white)}
.btn-outline-light{border:1px solid rgba(255,255,255,.8);color:var(--white)}
.welcome .actions{position:absolute;top:236px;width:100%;display:flex;justify-content:center;gap:20px}
.services{position:absolute;left:0;top:316px;width:1200px;height:230px}
.service-label{position:absolute;top:196px;width:160px;text-align:center;font-size:13px;font-weight:700;color:var(--ink-2);letter-spacing:1px}

/* videos */
.videos{position:absolute;left:0;top:1340px;width:1200px;height:390px;background:linear-gradient(90deg,var(--blue-bright) 0%,#1a8ccc 50%,var(--blue-mid) 100%)}
.videos h2{position:absolute;left:100px;top:46px;font-size:28px;font-weight:700;color:var(--white);letter-spacing:.5px}
.videos p{position:absolute;left:100px;top:100px;width:410px;font-size:12px;line-height:20px;color:var(--blue-pale)}
.videos .btn{position:absolute;left:100px;top:280px}
.video-frame{position:absolute;left:596px;top:30px;width:504px;height:330px;background:#111;box-shadow:0 6px 20px rgba(0,0,0,.3)}
.video-title{height:30px;line-height:30px;padding-left:12px;font-size:11px;font-weight:700;color:var(--white);letter-spacing:1px;background:#1a1a1a}
.video-still{position:absolute;left:0;top:30px;width:504px;height:266px;background:linear-gradient(135deg,#e9eef2 0%,#b9c7d3 50%,#6f8396 100%)}
.video-controls{position:absolute;left:0;bottom:0;width:504px;height:34px;background:#1b1b1b}

/* work & news */
.work{position:absolute;left:80px;top:1750px;width:640px}
.section-title{font-family:"Raleway",sans-serif;font-size:26px;font-weight:700;color:var(--ink-2);letter-spacing:.5px}
.pager{position:absolute;right:0;top:4px;display:flex;gap:6px}
.pager span{width:26px;height:26px;background:#d5d9dd;display:flex;align-items:center;justify-content:center}
.pager span + span{background:#9ba3aa}
.work-grid{position:absolute;left:0;top:66px;display:grid;grid-template-columns:repeat(3,200px);column-gap:20px;row-gap:42px}
.work-tile{width:200px;height:156px;position:relative}
.work-image{height:126px}
.work-caption{height:30px;line-height:30px;background:var(--ink-2);color:var(--white);font-size:10px;font-weight:700;text-align:center;letter-spacing:.5px}
.news{position:absolute;left:780px;top:1750px;width:340px}
.news-list{position:absolute;top:66px;left:0;width:340px}
.news-item{display:flex;gap:16px;height:104px;border-bottom:1px solid var(--line);padding-top:14px}
.news-date{width:60px;height:60px;background:var(--blue-bright);color:var(--white);text-align:center;font-size:11px;font-weight:700;line-height:15px;padding-top:8px}
.news-item h3{font-size:12px;font-weight:700;color:var(--ink-2);margin-top:6px}
.news-item a{font-size:11px;color:var(--blue-bright);text-decoration:none;font-weight:600}

/* partners */
.partners{position:absolute;left:0;top:2300px;width:1200px;height:160px;background:var(--grey-band);display:flex;align-items:center;justify-content:center;gap:18px}
.partner{width:120px;height:80px;background:#2b2f33;border:3px solid #5a6066}
.partner-arrow{width:30px;height:30px;display:flex;align-items:center;justify-content:center}

/* footer */
.site-footer{position:absolute;left:0;top:2460px;width:1200px;height:340px;background:#1c1f22;color:#a7adb3}
.footer-col{position:absolute;top:40px;font-size:11px;line-height:18px}
.footer-col h4{font-family:"Raleway",sans-serif;font-size:13px;font-weight:700;color:var(--white);letter-spacing:1px;margin-bottom:14px}
.footer-brand{font-family:"Raleway",sans-serif;font-weight:800;font-size:22px;color:var(--white);letter-spacing:3px;display:flex;align-items:center;gap:10px;margin-bottom:14px}
.footer-brand i{width:24px;height:24px;background:var(--blue-bright);display:block}
.field{width:200px;height:28px;background:#2b3035;border:1px solid #3c4248;margin:12px 0 10px}
.btn-small{display:inline-block;background:var(--blue-bright);color:var(--white);font-size:10px;font-weight:700;padding:5px 14px;letter-spacing:1px}
.contact-row{display:flex;align-items:center;gap:8px;margin-bottom:6px}
.social{display:flex;gap:10px;margin-top:8px}
.social span{width:18px;height:18px;border-radius:50%;background:#5d646b}
.footer-bottom{position:absolute;left:0;top:268px;width:1200px;text-align:center;font-size:10px;color:#8c9399;line-height:18px}
.footer-bottom nav{color:#c3c8cc;margin-bottom:4px;word-spacing:4px}
</style>
</head>
<body>

<header class="site-header">
  <div class="brand"><span class="brand-mark"></span><span class="brand-name">VELIROX</span></div>
  <div class="account-links"><span>▪ LOGIN</span><span>▪ REGISTER</span></div>
  <div class="search-box">Search
    <svg width="14" height="14" viewBox="0 0 14 14"><circle cx="6" cy="6" r="4.5" fill="none" stroke="#8c9298" stroke-width="1.5"/><line x1="9.5" y1="9.5" x2="13" y2="13" stroke="#8c9298" stroke-width="1.5"/></svg>
  </div>
</header>

<nav class="main-nav">
  <a href="#">HOME</a><a href="#">WORK</a><a href="#">EXPERTISE</a><a href="#">APPROACH</a><a href="#">CLIENTS</a><a href="#">ABOUT</a><a href="#">CONTACT</a>
</nav>

<section class="hero">
  <div class="hero-photo" role="img" aria-label="Hero photo of a hand touching a glowing interface showing the design, engineering, manufacturing and sourcing process"></div>
  <div class="slider-dots"><span></span><span></span><span></span><span></span></div>
</section>

<section class="welcome">
  <h1 class="heading">WELCOME TO VELIROX</h1>
  <p class="intro">We develop sustainable products from the first sketch to the final shipment. Our team combines design, engineering, manufacturing and sourcing to help partners bring clean energy ideas to market with care, speed and a clear focus on long lasting quality for every single client and project.</p>
  <div class="actions"><a class="btn btn-solid" href="#">LET'S GET STARTED</a><a class="btn btn-outline" href="#">READ MORE</a></div>
  <div class="services">
    <svg width="1200" height="190" viewBox="0 0 1200 190">
      <line x1="180" y1="90" x2="1020" y2="90" stroke="#c9d2da" stroke-width="3"/>
      <g fill="#0293ce" stroke="#ffffff" stroke-width="6">
        <circle cx="180" cy="90" r="66"/><circle cx="460" cy="90" r="66"/><circle cx="740" cy="90" r="66"/><circle cx="1020" cy="90" r="66"/>
      </g>
      <g fill="none" stroke="#c9d8e5" stroke-width="2">
        <circle cx="180" cy="90" r="76"/><circle cx="460" cy="90" r="76"/><circle cx="740" cy="90" r="76"/><circle cx="1020" cy="90" r="76"/>
      </g>
      <g fill="#ffffff"><polygon points="164,112 168,98 196,70 204,78 176,106"/><polygon points="160,116 164,104 172,110"/></g>
      <g fill="#ffffff">
        <circle cx="452" cy="96" r="15"/><circle cx="474" cy="76" r="9"/>
        <g stroke="#ffffff" stroke-width="6"><line x1="452" y1="74" x2="452" y2="118"/><line x1="430" y1="96" x2="474" y2="96"/><line x1="436" y1="80" x2="468" y2="112"/><line x1="468" y1="80" x2="436" y2="112"/></g>
        <circle cx="452" cy="96" r="6" fill="#0293ce"/><circle cx="474" cy="76" r="4" fill="#0293ce"/>
      </g>
      <g fill="#ffffff"><rect x="735" y="78" width="10" height="42" transform="rotate(45 740 90)"/><circle cx="756" cy="74" r="13"/><circle cx="762" cy="68" r="7" fill="#0293ce"/></g>
      <g fill="#ffffff"><circle cx="1020" cy="76" r="9"/><path d="M1002 112 a18 18 0 0 1 36 0z"/><circle cx="998" cy="82" r="7"/><path d="M984 110 a14 14 0 0 1 22 -10 v10z"/><circle cx="1042" cy="82" r="7"/><path d="M1056 110 a14 14 0 0 0 -22 -10 v10z"/></g>
    </svg>
    <div class="service-label" style="left:100px">DESIGN</div>
    <div class="service-label" style="left:380px">ENGINEERING</div>
    <div class="service-label" style="left:660px">MANUFACTURING</div>
    <div class="service-label" style="left:940px">SOURCING</div>
  </div>
</section>

<section class="videos">
  <h2 class="heading">PROJECT VIDEOS</h2>
  <p>Follow our projects from the drawing board to the production floor. These short films show how our engineers test ideas, refine prototypes and work with partners on solar and storage products. Watch how each step is planned, built and checked before a product reaches the customer. New films are added every month as projects move forward.</p>
  <a class="btn btn-outline-light" href="#">READ MORE</a>
  <div class="video-frame">
    <div class="video-title">VELIROX PROJECTS</div>
    <div class="video-still" role="img" aria-label="Video still of two engineers reviewing work at a computer"></div>
    <svg style="position:absolute;left:222px;top:133px" width="60" height="60" viewBox="0 0 60 60"><circle cx="30" cy="30" r="28" fill="#0555a3" fill-opacity=".85"/><polygon points="24,18 44,30 24,42" fill="#ffffff"/></svg>
    <div class="video-controls">
      <svg width="504" height="34" viewBox="0 0 504 34"><polygon points="14,10 26,17 14,24" fill="#ffffff"/><rect x="40" y="15" width="360" height="4" fill="#555"/><rect x="40" y="15" width="60" height="4" fill="#0293ce"/><rect x="420" y="11" width="14" height="12" fill="none" stroke="#ffffff" stroke-width="2"/><rect x="450" y="11" width="16" height="12" fill="none" stroke="#ffffff" stroke-width="2"/></svg>
    </div>
  </div>
</section>

<section class="work">
  <h2 class="section-title">OUR WORK</h2>
  <div class="pager"><span><svg width="10" height="10"><polygon points="7,1 2,5 7,9" fill="#fff"/></svg></span><span><svg width="10" height="10"><polygon points="3,1 8,5 3,9" fill="#fff"/></svg></span></div>
  <div class="work-grid">
    <div class="work-tile"><div class="work-image" role="img" aria-label="Photo of mechanical engineering work" style="background:linear-gradient(135deg,#4a5560,#9aa7b3)"></div><div class="work-caption">MECHANICAL ENGINEERING</div></div>
    <div class="work-tile"><div class="work-image" role="img" aria-label="Photo of prototype parts" style="background:linear-gradient(135deg,#6b6f74,#c9c2b6)"></div><div class="work-caption">PROTOTYPE DEVELOPMENT</div></div>
    <div class="work-tile"><div class="work-image" role="img" aria-label="Photo of an electronic circuit board" style="background:linear-gradient(135deg,#2f5d3a,#d4b03c)"></div><div class="work-caption">ELECTRICAL ENGINEERING</div></div>
    <div class="work-tile"><div class="work-image" role="img" aria-label="Photo of laboratory science equipment" style="background:linear-gradient(135deg,#1f4f7d,#85cae6)"></div><div class="work-caption">SCIENCE &amp; TECHNOLOGY</div></div>
    <div class="work-tile"><div class="work-image" role="img" aria-label="Photo of a manufacturing line" style="background:linear-gradient(135deg,#3b4a56,#a4b6c4)"></div><div class="work-caption">MANUFACTURING</div></div>
    <div class="work-tile"><div class="work-image" role="img" aria-label="Industrial design sketches" style="background:linear-gradient(135deg,#e8ebee,#aeb6be)"></div><div class="work-caption">INDUSTRIAL DESIGN</div></div>
  </div>
</section>

<section class="news">
  <h2 class="section-title">LATEST NEWS</h2>
  <div class="pager"><span><svg width="10" height="10"><polygon points="7,1 2,5 7,9" fill="#fff"/></svg></span><span><svg width="10" height="10"><polygon points="3,1 8,5 3,9" fill="#fff"/></svg></span></div>
  <div class="news-list">
    <article class="news-item"><div class="news-date">AUG 2<br>2014</div><div><h3>LAUNCH OF WEBSITE</h3><a href="#">Read More</a></div></article>
    <article class="news-item"><div class="news-date">JUN 1<br>2014</div><div><h3>FIRST PROJECT INITIATED</h3><a href="#">Read More</a></div></article>
    <article class="news-item"><div class="news-date">MAY 1<br>2014</div><div><h3>ESTABLISHMENT OF VELIROX APS</h3><a href="#">Read More</a></div></article>
    <article class="news-item" style="border-bottom:none"><div class="news-date">AUG 2<br>2014</div><div><h3>LAUNCH OF WEBSITE</h3><a href="#">Read More</a></div></article>
  </div>
</section>

<section class="partners" aria-label="Partners">
  <span class="partner-arrow"><svg width="14" height="20"><polygon points="12,2 3,10 12,18" fill="#3a3f44"/></svg></span>
  <div class="partner"></div><div class="partner"></div><div class="partner"></div><div class="partner"></div><div class="partner"></div><div class="partner"></div><div class="partner"></div>
  <span class="partner-arrow"><svg width="14" height="20"><polygon points="2,2 11,10 2,18" fill="#3a3f44"/></svg></span>
</section>

<footer class="site-footer">
  <div class="footer-col" style="left:100px;width:220px">
    <div class="footer-brand"><i></i>VELIROX</div>
    <p>Velirox is a development company working with green energy and sustainable products, from design and engineering to manufacturing and sourcing for partners.</p>
  </div>
  <div class="footer-col" style="left:360px;width:220px">
    <h4>SUBSCRIBE OUR NEWSLETTER</h4>
    <p>Register your email to get news about our company</p>
    <div class="field"></div>
    <span class="btn-small">SIGN UP</span>
  </div>
  <div class="footer-col" style="left:620px;width:260px">
    <h4>LATEST TWEETS</h4>
    <div class="contact-row" style="align-items:flex-start"><svg width="14" height="14" style="margin-top:2px;flex:none"><rect width="14" height="14" fill="#0293ce"/></svg><p>New solar storage prototype now in testing at our workshop. Read the full update on our blog today.<br><span style="color:#0293ce">2 days ago</span></p></div>
  </div>
  <div class="footer-col" style="left:920px;width:200px">
    <h4>CONTACT US</h4>
    <div class="contact-row"><svg width="12" height="12" viewBox="0 0 12 12"><path d="M2 1 L5 1 L6 4 L4.5 5 A7 7 0 0 0 7 7.5 L8 6 L11 7 L11 10 Q11 11 10 11 A9 9 0 0 1 1 2 Q1 1 2 1z" fill="#a7adb3"/></svg>+45 71 82 64 93</div>
    <div class="contact-row"><svg width="12" height="10" viewBox="0 0 12 10"><rect x=".5" y=".5" width="11" height="9" fill="none" stroke="#a7adb3"/><polyline points="1,1 6,6 11,1" fill="none" stroke="#a7adb3"/></svg>info@velirox.com</div>
    <div class="social"><span></span><span></span><span></span></div>
  </div>
  <div class="footer-bottom">
    <nav>Home | Work | Expertise | Approach | Clients | About | Contact</nav>
    <p>Velirox ApS © 2014 . All rights reserved.</p>
  </div>
</footer>

</body>
</html>
```